Local fast-growing company in the service sector

We are looking for a modern business card design, which should also appear on our letterheads

Target Market(s)

Private and industrial sectors

Contact Information for Business Card

Vorname Name
Kellberger Str. 18
71364 Winnenden
Tel.: 07146-839214-0
Name@agentur-kvtl.de

Colors
9d9d9d
919191
aaaaaa

Requirements
Must have
• The logo (file) in silver

```html
<!DOCTYPE html>
<html lang="de">
<head>
<meta charset="utf-8">
<title>KVTL Visitenkarte</title>
<link rel="stylesheet" href="https://fonts.googleapis.com/css2?family=Figtree:wght@400;500;700&display=swap">
<style>
  :root {
    --backdrop: #2e2e2e;
    --white: #ffffff;
    --silver-light: #d2d3d5;
    --silver: #aaaaaa;
    --silver-mid: #9d9d9d;
    --silver-dark: #6f7072;
    --logo-grey: #8d8d8d;
    --back-mark: #707173;
    --icon-cut: #8e8f91;
  }
  * { box-sizing: border-box; margin: 0; padding: 0; }
  html, body { width: 1200px; height: 960px; overflow: hidden; }
  body {
    background: var(--backdrop);
    font-family: "Figtree", sans-serif;
    position: relative;
  }
  .card {
    position: absolute;
    width: 600px;
    height: 342px;
    border-radius: 20px;
    overflow: hidden;
  }
  .card-front {
    left: 302px; top: 129px;
    background: linear-gradient(100deg, #7b7c7e 0%, #a9aaac 40%, #b9babc 60%, #7e7f81 100%);
  }
  .card-back {
    left: 299px; top: 488px;
    background: linear-gradient(90deg, var(--silver-light) 0%, #c4c5c7 35%, #a3a4a6 60%, var(--silver-dark) 100%);
  }
  .front-flap { position: absolute; inset: 0; }
  .brand {
    position: absolute;
    left: 0; right: 0; top: 70px;
    display: flex; justify-content: center; align-items: center; gap: 14px;
  }
  .brand-square {
    width: 30px; height: 30px;
    background: var(--logo-grey);
  }
  .brand-name {
    font-weight: 700;
    font-size: 52px;
    line-height: 1;
    letter-spacing: 2px;
    color: var(--logo-grey);
  }
  .holder {
    position: absolute;
    left: 30px; top: 259px;
    color: var(--white);
  }
  .holder-name { font-size: 19px; font-weight: 700; line-height: 22px; margin-bottom: 1px; }
  .holder-line { font-size: 14px; line-height: 19px; }
  .contact {
    position: absolute;
    right: 30px; top: 262px;
    list-style: none;
    color: var(--white);
    font-size: 14px;
  }
  .contact li {
    display: flex; justify-content: flex-end; align-items: center;
    gap: 8px; height: 19px;
  }
  .contact svg { width: 13px; height: 13px; fill: var(--white); }
  .back-name {
    position: absolute;
    left: 0; right: 0; top: 110px;
    text-align: center;
    font-weight: 700;
    font-size: 90px;
    line-height: 1;
    letter-spacing: 4px;
    color: var(--back-mark);
  }
  .back-url {
    position: absolute;
    left: 0; right: 0; top: 290px;
    text-align: center;
    font-size: 14px;
    line-height: 1;
    letter-spacing: 3px;
    color: var(--white);
  }
</style>
</head>
<body>
  <section class="card card-front">
    <svg class="front-flap" viewBox="0 0 600 342" width="600" height="342" aria-hidden="true">
      <defs>
        <linearGradient id="flapFill" x1="0" y1="0" x2="1" y2="0">
          <stop offset="0" stop-color="#ffffff"/>
          <stop offset="0.6" stop-color="#ffffff"/>
          <stop offset="1" stop-color="#d6d6d6"/>
        </linearGradient>
      </defs>
      <path d="M0,0 H600 V38 L352,286 Q300,314 248,286 L0,38 Z" fill="#c5c6c8"/>
      <path d="M0,0 H600 V22 L350,276 Q300,304 250,276 L0,22 Z" fill="url(#flapFill)"/>
    </svg>
    <div class="brand">
      <span class="brand-square"></span>
      <span class="brand-name">KVTL</span>
    </div>
    <div class="holder">
      <p class="holder-name">Jonas Keller</p>
      <p class="holder-line">Kellberger Str. 18</p>
      <p class="holder-line">71364 Winnenden</p>
    </div>
    <ul class="contact">
      <li>07146-839214-0
        <svg viewBox="0 0 24 24"><path d="M6.6 10.8a15.1 15.1 0 0 0 6.6 6.6l2.2-2.2a1 1 0 0 1 1-.25 11.4 11.4 0 0 0 3.6.57 1 1 0 0 1 1 1V20a1 1 0 0 1-1 1A17 17 0 0 1 3 4a1 1 0 0 1 1-1h3.5a1 1 0 0 1 1 1c0 1.25.2 2.45.57 3.57a1 1 0 0 1-.25 1z"/></svg>
      </li>
      <li>jonas@agentur-kvtl.de
        <svg viewBox="0 0 24 24"><path d="M2 5h20v14H2z"/><path d="M3 6l9 7 9-7" fill="none" stroke="var(--icon-cut)" stroke-width="1.6"/></svg>
      </li>
      <li>www.agentur-kvtl.de
        <svg viewBox="0 0 24 24"><circle cx="12" cy="12" r="10"/><path d="M2 12h20M12 2c3 3 3 17 0 20M12 2c-3 3-3 17 0 20" fill="none" stroke="var(--icon-cut)" stroke-width="1.4"/></svg>
      </li>
    </ul>
  </section>

  <section class="card card-back">
    <p class="back-name">KVTL</p>
    <p class="back-url">WWW.AGENTUR-KVTL.DE</p>
  </section>
</body>
</html>
```